Creative, fresh business card design for Ripplecraft Facades

We need a fresh, creative business card design for Ripplecraft Facades. We are the manufacturer of Ripplecraft Facades in Australia. Wall panels are 2400 x 1200mm panels made from MDF and feature 3D patterns on the face of the panel. The colours to be used are green, silver/grey and white RGB
Red 187
Green 207
Blue 65.

An idea is to possibly use a watermark of one of our designs as a background (like on the "Grids" design on the left hand side of page 2 of our brochure).

Target Market(s)

Interior designers, architects, builders and home renovators

Industry/Entity Type

Business

Contact Information for Business Card

Details to go on the card are:
Our logo (attached),
Slogan: "Decorative panels for interiors and exteriors",
Contact name,
Position,
Mobile phone number,
Business address,
Business phone,
Business fax,
Website and
Email address.

I have attached a few images of our panels and our brochure for reference.

The colours of the business card should feature our logo colours which are: RGB
Red 187
Green 207
Blue 65

Requirements
Must have
• Very modern fonts and design. Some of the designs shown especially the "Prisms" design which is a popular design.
Nice to have
• Creative but simple design. Very contemporary.
Should not have
• Anything ornate or old fashioned.

```html
<!DOCTYPE html>
<html lang="en">
<head>
<meta charset="utf-8">
<title>Ripplecraft Facades – Business Card</title>
<link href="https://fonts.googleapis.com/css2?family=Source+Sans+3:wght@400;600;700&display=swap" rel="stylesheet">
<style>
  :root {
    --stage: #000000;
    --brand-green: #bbcf41;
    --card-white: #ffffff;
    --ink: #1c1c1c;
    --tag-grey: #9a9a9a;
    --pattern-pink: #f08a86;
    --pattern-rose: #f6c9c6;
  }
  * { margin: 0; padding: 0; box-sizing: border-box; }
  html, body { width: 1200px; height: 900px; overflow: hidden; background: var(--stage); }
  body { position: relative; font-family: "Source Sans 3", Arial, sans-serif; }

  .card { position: absolute; top: 275px; width: 477px; height: 293px; overflow: hidden; }

  .card-front { left: 116px; background: var(--card-white); border-radius: 0 56px 0 56px; }
  .card-back { left: 622px; top: 276px; height: 292px; background: var(--brand-green); border-radius: 56px 0 56px 0; }

  .panel-texture {
    position: absolute; left: 0; top: 0; width: 150px; height: 100%;
    background:
      linear-gradient(90deg, rgba(255,255,255,0) 0%, rgba(255,255,255,0.2) 45%, #fff 100%),
      linear-gradient(180deg, var(--pattern-pink) 0%, var(--pattern-rose) 45%, #f3dcdc 100%);
  }

  .contact-block { position: absolute; right: 33px; text-align: right; color: var(--ink); }
  .person-name { top: 39px; font-size: 18px; font-weight: 700; line-height: 22px; }
  .person-role { top: 58px; font-size: 13px; line-height: 16px; }
  .address { top: 102px; font-size: 13px; line-height: 15px; }

  .contact-list { position: absolute; right: 30px; top: 170px; list-style: none; }
  .contact-list li {
    display: flex; justify-content: flex-end; align-items: center;
    font-size: 13px; height: 19.8px; color: var(--ink);
  }
  .contact-list svg { width: 10px; height: 10px; margin-left: 8px; fill: var(--brand-green); }

  .brand-lockup { position: absolute; display: flex; align-items: center; font-weight: 700; }
  .brand-mark { display: inline-block; margin-right: 8px; }
  .card-front .brand-lockup { left: 40px; top: 198px; color: var(--brand-green); font-size: 19px; }
  .card-front .brand-mark { width: 16px; height: 16px; background: var(--brand-green); }
  .card-back .brand-lockup { left: 0; right: 0; top: 112px; justify-content: center; color: var(--card-white); font-size: 30px; }
  .card-back .brand-mark { width: 24px; height: 24px; background: var(--card-white); margin-right: 12px; }

  .slogan {
    position: absolute; font-size: 11px; letter-spacing: 2.2px; line-height: 12px; text-align: center;
  }
  .card-front .slogan { left: 38px; top: 240px; width: 184px; color: var(--tag-grey); }
  .card-back .slogan { left: 0; right: 0; top: 197px; color: var(--card-white); font-size: 12px; line-height: 15px; }
</style>
</head>
<body>

<section class="card card-front">
  <div class="panel-texture" role="img" aria-label="Faded pink 3D pyramid wall panel texture"></div>

  <div class="brand-lockup"><span class="brand-mark"></span>Ripplecraft Facades</div>
  <p class="slogan">decorative panels for<br>interiors &amp; landscapes</p>

  <p class="contact-block person-name">Marcus Hale</p>
  <p class="contact-block person-role">Managing Director</p>
  <p class="contact-block address">48 Kiln Street, Brookvale<br>Australia, NSW 2100</p>

  <ul class="contact-list">
    <li>0412-385-920
      <svg viewBox="0 0 10 10"><path d="M2.5 0h5a1 1 0 0 1 1 1v8a1 1 0 0 1-1 1h-5a1 1 0 0 1-1-1V1a1 1 0 0 1 1-1zm.5 1.5v6h4v-6z"/></svg></li>
    <li>(02)-9938-4471
      <svg viewBox="0 0 10 10"><path d="M2 0.5l1.8 2-1 1.2a6 6 0 0 0 3.5 3.5l1.2-1 2 1.8-1.2 1.5C5 9.5 0.5 5 0.5 1.7z"/></svg></li>
    <li>02-9938-4472
      <svg viewBox="0 0 10 10"><path d="M2.5 0h4v3h-4zM1 3.5h8v5H1zM3 5h4v1H3zm0 1.8h4v.8H3z"/></svg></li>
    <li>hello@ripplecraft.example
      <svg viewBox="0 0 10 10"><path d="M0.5 2h9v6h-9zm1 1l3.5 2.5L8.5 3z"/></svg></li>
    <li>www.ripplecraft.example
      <svg viewBox="0 0 10 10"><circle cx="5" cy="5" r="4.5"/></svg></li>
  </ul>
</section>

<section class="card card-back">
  <div class="brand-lockup"><span class="brand-mark"></span>Ripplecraft Facades</div>
  <p class="slogan">decorative panels for<br>interiors &amp; landscapes</p>
</section>

</body>
</html>
```